Varentoria Business Card and Letter Head

We are a leadership assessment consultancy based in Sydney, Australia. We help executive-level decison-makers select leaders for more senior level roles in corporate and government organisations. Our methodology is based on the latest research from the field of neuroscience.
We need a business card design and matching letter head that presents our company, Varentoria, as a:
1. trusted adviser to senior executive-level decison makers
2. niche consultancy who are experts in the field of assessing leadership talent
3. results-focused solution provider who balance scientific methods with pragmatic solutions
The following company details should be used in all designs:
Company Name: Varentoria
Details (for business card):
Derek Hanford
Prime Capacity Officer
Level 29, Marlow Tower
7 Marlow Square
Sydney, NSW 2000 Australia
Phone: 1300 582 714
Mobile: 0412 637 258
Email: derek.hanford@varentoria-example.com.au
Website: varentoria-example.com.au
I have attached the logo for Varentoria (for both a white and black background) - your business card and letter head designs must incoporate this logo and colour scheme.
Thanks for your interest in this project, I'm looking forward to receiving your ideas.
Regards,
Derek
Target Market(s)
Executive-level decison-makers in corporate and government organisations (e.g., CEO, VP, Head of Human Resources)
Industry/Entity Type
Leadership
Look and feel

```html
<!DOCTYPE html>
<html lang="en">
<head>
<meta charset="UTF-8">
<title>Varentoria Business Card</title>
<link href="https://fonts.googleapis.com/css2?family=Open+Sans:wght@400;600;700&display=swap" rel="stylesheet">
<style>
  :root {
    --page-bg: #ecebe8;
    --card-white: #ffffff;
    --brand-red: #c0281c;
    --brand-red-deep: #5a120c;
    --ink: #2e2e2e;
    --ink-soft: #4a4a4a;
    --swoosh-grey: #3b3b3d;
    --faint-grey: #ececec;
    --on-red: #ffffff;
  }
  * { margin: 0; padding: 0; box-sizing: border-box; }
  html, body {
    width: 1200px;
    height: 1094px;
    overflow: hidden;
    background: var(--page-bg);
    font-family: "Open Sans", Arial, sans-serif;
  }
  .canvas {
    position: relative;
    width: 1200px;
    height: 1094px;
  }
  .card {
    position: absolute;
    left: 220px;
    width: 760px;
    height: 434px;
    border-radius: 30px;
    overflow: hidden;
    box-shadow: 0 6px 18px rgba(0,0,0,0.18);
  }
  .card-front { top: 80px; background: var(--card-white); }
  .card-back { top: 590px; background: var(--brand-red); }

  .front-shapes { position: absolute; inset: 0; }

  .brand {
    position: absolute;
    display: flex;
    align-items: center;
  }
  .brand-mark {
    display: block;
    background: var(--ink);
  }
  .brand-name {
    font-weight: 600;
    color: var(--ink);
    letter-spacing: -0.5px;
  }
  .card-front .brand { left: 46px; top: 78px; gap: 16px; }
  .card-front .brand-mark { width: 36px; height: 36px; }
  .card-front .brand-name { font-size: 46px; }

  .faint-square {
    position: absolute;
    right: 70px;
    top: 40px;
    width: 110px;
    height: 110px;
    border: 14px solid var(--faint-grey);
  }

  .person { position: absolute; left: 48px; top: 178px; }
  .person-name {
    font-size: 24px;
    font-weight: 700;
    color: var(--brand-red);
    line-height: 1.2;
  }
  .person-title {
    font-size: 15px;
    color: var(--ink);
    margin-top: 2px;
  }
  .address {
    position: absolute;
    left: 48px;
    top: 252px;
    font-size: 15.5px;
    font-style: normal;
    line-height: 1.5;
    color: var(--ink-soft);
  }

  .contacts {
    position: absolute;
    right: 34px;
    top: 290px;
    list-style: none;
    color: var(--on-red);
    font-size: 16px;
    text-align: right;
    line-height: 1.55;
  }
  .contacts li {
    display: flex;
    justify-content: flex-end;
    align-items: center;
    gap: 8px;
  }
  .contacts svg { width: 14px; height: 14px; flex: none; }

  .card-back .brand {
    left: 0; right: 0; top: 0; bottom: 0;
    justify-content: center;
    gap: 26px;
  }
  .card-back .brand-mark { width: 60px; height: 60px; background: var(--brand-red-deep); }
  .card-back .brand-name { font-size: 84px; color: var(--brand-red-deep); }
</style>
</head>
<body>
<main class="canvas">

  <section class="card card-front" aria-label="Business card front">
    <svg class="front-shapes" viewBox="0 0 760 434" preserveAspectRatio="none" aria-hidden="true">
      <path d="M0,380 C300,370 560,300 760,170 L760,434 L0,434 Z" fill="var(--brand-red)"/>
      <path d="M0,360 C220,352 420,318 580,268 C420,326 220,362 0,372 Z" fill="var(--swoosh-grey)"/>
    </svg>

    <span class="faint-square" aria-hidden="true"></span>

    <div class="brand">
      <span class="brand-mark" aria-hidden="true"></span>
      <span class="brand-name">Varentoria</span>
    </div>

    <div class="person">
      <p class="person-name">Derek Hanford</p>
      <p class="person-title">Prime Capacity Officer</p>
    </div>

    <address class="address">
      Level 29, Marlow Tower<br>
      7 Marlow Square<br>
      Sydney, NSW 2000 Australia
    </address>

    <ul class="contacts">
      <li>
        <svg viewBox="0 0 16 16" aria-hidden="true"><circle cx="8" cy="8" r="7.5" fill="#fff"/><path d="M5 4.5l1.6-.3.9 2-1 .8c.5 1.1 1.3 1.9 2.4 2.4l.8-1 2 .9-.3 1.6c-3.6.2-6.6-2.8-6.4-6.4z" fill="var(--brand-red)"/></svg>
        1300 582 714
      </li>
      <li>
        <svg viewBox="0 0 16 16" aria-hidden="true"><rect x="4" y="1" width="8" height="14" rx="1.5" fill="#fff"/><rect x="5.5" y="3" width="5" height="7" fill="var(--brand-red)"/></svg>
        0412 637 258
      </li>
      <li>
        <svg viewBox="0 0 16 16" aria-hidden="true"><rect x="1" y="3" width="14" height="10" fill="#fff"/><path d="M1 3l7 6 7-6" fill="none" stroke="var(--brand-red)" stroke-width="1.3"/></svg>
        derek.hanford@varentoria-example.com.au
      </li>
      <li>
        <svg viewBox="0 0 16 16" aria-hidden="true"><circle cx="8" cy="8" r="7" fill="#fff"/><path d="M1 8h14M8 1c-3 3.5-3 10.5 0 14M8 1c3 3.5 3 10.5 0 14" fill="none" stroke="var(--brand-red)" stroke-width="1"/></svg>
        varentoria-example.com.au
      </li>
    </ul>
  </section>

  <section class="card card-back" aria-label="Business card back">
    <div class="brand">
      <span class="brand-mark" aria-hidden="true"></span>
      <span class="brand-name">Varentoria</span>
    </div>
  </section>

</main>
</body>
</html>
```